Web site for a company that sells Pinball machines

We need a website that is an online shopping experience for a Store that sells pinball machines and accessories. The name of the store is called "Gadget Arcade." The store it self has a showroom, but we would also like to have an Internet e-commerce presence. We pinball machines made by Vexler pinball. You can visit their website and see their current list of machines as well as their website for the machines that we are going to carry in our store. Their website is Vexlerpinball.com. I am able to use their machine photos as well as their machine brochure PDF files. I am also able to use their logo on my website two list it as a Vexler Authorized Dealer.
This website design needs to be funky, fun, very technologically oriented and modern. The people buying machines our spending anywhere between $5000 and $15,000 on one machine. These Are high-end buyers who are also usually fairly tech savvy or at least enjoy technology and graphics.
Attachments: I have attached photographs of some of my own machines which may be used in the website. I've also attached some downloaded files from Vexler pinball.com as well as some of their PDF files for brochures. I will carry all of their current models they have listed under games. Not the archived games. I have included one of their machines called Thunderwolf Limited edition in my photograph attachments. The rest of the photos are just random pictures that I have taken myself and maybe used to build the site. Lastly I have attached my logo which I am not super crazy about so I will also be posting a contest to redesign this logo. Tons more of my own pinball photos are available.
I would like for people to be able to purchase machines and accessories from the website, but also inform them to our actual showroom.
Updates
Project Deadline Extended Reason: Hello. We have extended five days due to some complications during the construction of our actual building. We were unable to participate in this web design during this time and so unfortunately were not able give feedback appropriately. We are back on track and will provide feedback to the designers who have designed up until this point. We will still be interested in seeing new submissions, however; this extension will give us a chance to provide feedback and coordinate the website appropriately. Thank you so much for your submissions and your patience!!!!Gadget Arcade Added Friday, April 21, 2017
Target Market(s)
Target market is 16 to 75. Techy individuals to enjoy gaming technology video animation and Vegas style twinkle
Industry/Entity Type
It Company
Coding
Coded - Design and coding required
Number of Pages Required
3 page
Font styles to use
Look and feel
Each slider illustrates characteristics of the customer's brand and the style your logo design should communicate.

```html
<!DOCTYPE html>
<html lang="en">
<head>
<meta charset="utf-8">
<title>Gadget Arcade – Pinball Machines</title>
<link href="https://fonts.googleapis.com/css2?family=Open+Sans:wght@400;600;700&display=swap" rel="stylesheet">
<style>
:root{
  --red:#d2171e;
  --red-dark:#a50f14;
  --ink:#333333;
  --muted:#8a8a8a;
  --cream:#f3efe6;
  --slate:#5a5a5a;
  --band:#e6e6e6;
  --white:#ffffff;
  --line:#dddddd;
  --night:#2a1a1c;
}
*{box-sizing:border-box;margin:0;padding:0}
html,body{width:1200px;height:2548px;overflow:hidden}
body{font-family:"Open Sans",Arial,sans-serif;color:var(--ink);background:var(--white);position:relative}
.abs{position:absolute}

/* header */
.site-header{position:absolute;left:0;top:0;width:1200px;height:176px;background:var(--white)}
.cart{left:128px;top:66px;display:flex;align-items:center;gap:10px;font-size:13px;color:var(--muted)}
.cart b{color:#7a2a8a;font-weight:600}
.brand{left:480px;top:22px;width:240px;height:120px;display:flex;align-items:center;justify-content:center;gap:12px}
.brand-dot{width:34px;height:34px;border-radius:50%;background:var(--red)}
.brand-name{font-size:28px;font-weight:700;color:var(--ink);letter-spacing:.5px}
.search{left:860px;top:60px;width:212px;height:32px;border:1px solid var(--line);border-radius:3px;display:flex;align-items:center;justify-content:space-between;padding:0 10px;font-size:12px;color:#aaa}

/* nav */
.main-nav{left:100px;top:176px;width:1000px;height:42px;background:var(--red);display:flex;align-items:stretch;padding:0 28px}
.main-nav::before,.main-nav::after{content:"";position:absolute;top:8px;width:40px;height:42px;background:var(--red-dark);z-index:-1}
.main-nav::before{left:-28px}
.main-nav::after{right:-28px}
.main-nav a{flex:1;color:var(--white);text-decoration:none;font-size:14px;display:flex;align-items:center;justify-content:center}
.main-nav a.active{background:#1e1e1e;flex:0 0 90px}

/* hero */
.hero{left:0;top:218px;width:1200px;height:802px;background:radial-gradient(ellipse at 50% 40%,#6a3a36 0%,#3b2024 45%,#1c1114 100%)}
.hero-frame{left:132px;top:232px;width:936px;height:472px;border:6px solid var(--white);border-radius:22px;background:linear-gradient(120deg,#4a2e2a,#a0605a 35%,#d9a56a 55%,#6b3a44 80%,#2e1c22)}
.feature{width:300px;text-align:center;color:var(--white)}
.feature-disc{width:176px;height:176px;margin:0 auto;border-radius:50%;border:6px solid var(--white)}
.feature h3{font-size:17px;font-weight:400;margin-top:18px}
.feature p{font-size:11px;line-height:17px;color:#d9cfcf;margin-top:8px;padding:0 14px}

/* products */
.products{left:0;top:1020px;width:1200px;height:680px;background:var(--cream)}
.section-title{width:1200px;text-align:center;font-size:30px;font-weight:600}
.section-lede{width:1200px;text-align:center;font-size:11px;line-height:17px;color:var(--muted)}
.product-card{width:304px;height:448px;top:1192px;background:var(--white);border:1px solid #e6e1d6;text-align:center}
.product-shot{width:150px;height:236px;margin:34px auto 0;border-radius:6px;background:linear-gradient(180deg,#3a2a5a,#6b3f8e 45%,#2b2338)}
.product-card h4{font-size:15px;font-weight:400;margin-top:34px}
.price{font-size:15px;font-weight:700;margin-top:6px}
.buy{display:inline-block;margin-top:14px;background:var(--red);color:var(--white);font-size:12px;padding:8px 24px;border-radius:16px}

/* games */
.games{left:0;top:1700px;width:1200px;height:460px;background:var(--slate)}
.games .section-title{color:var(--white)}
.games .section-lede{color:#cfcfcf}
.game-card{top:1900px;width:234px;height:196px;background:var(--white);padding:6px}
.game-shot{height:154px}
.game-card span{display:flex;align-items:center;gap:6px;font-size:12px;padding:8px 4px 0}
.game-card i{width:12px;height:12px;border-radius:50%;background:var(--red)}

/* perks */
.perks{left:0;top:2160px;width:1200px;height:130px;background:var(--band);display:flex;justify-content:space-between;padding:0 128px}
.perk{display:flex;gap:14px;margin-top:34px;width:270px}
.perk h5{font-size:14px;font-weight:600;color:var(--red)}
.perk p{font-size:11px;line-height:16px;color:var(--muted);margin-top:4px}

/* footer */
.site-footer{left:0;top:2290px;width:1200px;height:210px;background:var(--white);display:flex;gap:38px;padding:30px 128px 0}
.site-footer h6{font-size:11px;font-weight:700;letter-spacing:.5px;margin-bottom:12px}
.site-footer li{list-style:none;font-size:10px;line-height:17px;color:var(--muted)}
.newsletter{width:250px}
.newsletter p{font-size:10px;color:var(--muted);line-height:15px}
.newsletter .field{margin-top:10px;height:28px;border:1px solid var(--line);font-size:10px;color:#aaa;padding:7px 8px}
.newsletter .send{margin-top:10px;display:inline-block;background:var(--red);color:var(--white);font-size:10px;padding:6px 16px;border-radius:14px}
.col{width:120px}
.store{margin-left:auto;width:170px}
.store .name{color:var(--red);font-weight:600;font-size:11px}
.socials{display:flex;gap:8px;margin-top:10px}
.socials i{width:20px;height:20px;border-radius:50%;background:#777}
.legal{left:0;top:2500px;width:1200px;height:48px;border-top:1px solid var(--line);display:flex;align-items:center;justify-content:space-between;padding:0 128px;font-size:10px;color:var(--muted)}
</style>
</head>
<body>

<header class="site-header">
  <div class="abs cart">
    <svg width="18" height="16" viewBox="0 0 18 16"><path d="M1 2h3l2 9h9l2-7H5" fill="none" stroke="#777" stroke-width="1.6"/><circle cx="7" cy="14" r="1.4" fill="#777"/><circle cx="14" cy="14" r="1.4" fill="#777"/></svg>
    My Cart: <b>00 Items</b>
  </div>
  <div class="abs brand"><span class="brand-dot"></span><span class="brand-name">Gadget Arcade</span></div>
  <div class="abs search">Search
    <svg width="12" height="12" viewBox="0 0 12 12"><circle cx="5" cy="5" r="3.6" fill="none" stroke="#666" stroke-width="1.4"/><path d="M8 8l3 3" stroke="#666" stroke-width="1.4"/></svg>
  </div>
</header>

<nav class="abs main-nav">
  <a class="active">Home</a><a>About Us</a><a>Games</a><a>Community</a><a>Videos</a><a>Support</a><a>Buy</a><a>News</a>
</nav>

<section class="abs hero" role="img" aria-label="Blurred photo of a pinball showroom floor"></section>
<div class="abs hero-frame" role="img" aria-label="Photo of a row of lit pinball machines in the showroom"></div>

<div class="abs feature" style="left:110px;top:616px">
  <div class="feature-disc" role="img" aria-label="Thunderwolf playfield artwork" style="background:radial-gradient(circle,#e0a040,#8a3a2a)"></div>
  <h3>Thunderwolf</h3>
  <p>Limited edition cabinet with custom lights, mirror backglass and a loud stereo sound pack.</p>
</div>
<div class="abs feature" style="left:450px;top:616px">
  <div class="feature-disc" role="img" aria-label="Midnight Hero 66 playfield artwork" style="background:radial-gradient(circle,#c060c0,#3a2a6a)"></div>
  <h3>Midnight Hero 66</h3>
  <p>Retro comic styled table with bright ramps, fast flippers and a classic villain lineup.</p>
</div>
<div class="abs feature" style="left:750px;top:616px">
  <div class="feature-disc" role="img" aria-label="Realm of Crowns playfield artwork" style="background:radial-gradient(circle,#e0c060,#5a3a1a)"></div>
  <h3>Realm of Crowns</h3>
  <p>Epic fantasy machine with castle toys, dragon modes and deep rule sets for experts.</p>
</div>

<section class="abs products"></section>
<h2 class="abs section-title" style="left:0;top:1064px">Our Products</h2>
<p class="abs section-lede" style="left:0;top:1118px">Browse our showroom lineup of new pinball machines, shipped and set up by our team.<br>Every table is tested, leveled and ready to play the day it arrives.</p>

<div class="abs product-card" style="left:128px">
  <div class="product-shot" role="img" aria-label="Pinball machine product photo"></div>
  <h4>Accuscat Cupidatat</h4><div class="price">$5800.00</div><span class="buy">Buy Now Today</span>
</div>
<div class="abs product-card" style="left:448px">
  <div class="product-shot" role="img" aria-label="Pinball machine product photo"></div>
  <h4>Accuscat Cupidatat</h4><div class="price">$9800.00</div><span class="buy">Buy Now Today</span>
</div>
<div class="abs product-card" style="left:768px">
  <div class="product-shot" role="img" aria-label="Pinball machine product photo"></div>
  <h4>Accuscat Cupidatat</h4><div class="price">$15,000.00</div><span class="buy">Buy Now Today</span>
</div>

<section class="abs games"></section>
<h2 class="abs section-title" style="left:0;top:1768px;color:#fff">Games</h2>
<p class="abs section-lede" style="left:0;top:1822px;color:#cfcfcf">Explore every current Vexler title we carry, from music legends to movie blockbusters.<br>Visit our showroom to play them all before you buy.</p>

<div class="abs game-card" style="left:132px"><div class="game-shot" role="img" aria-label="Ironclad game artwork" style="background:linear-gradient(135deg,#2a3a5a,#8a5a3a)"></div><span><i></i>Ironclad</span></div>
<div class="abs game-card" style="left:380px"><div class="game-shot" role="img" aria-label="Thunderwolf game artwork" style="background:linear-gradient(135deg,#6a2a3a,#d08040)"></div><span><i></i>Thunderwolf</span></div>
<div class="abs game-card" style="left:628px"><div class="game-shot" role="img" aria-label="Spectre Squad game artwork" style="background:linear-gradient(135deg,#3a5a3a,#a0a0c0)"></div><span><i></i>Spectre Squad</span></div>
<div class="abs game-card" style="left:872px"><div class="game-shot" role="img" aria-label="Starblazer game artwork" style="background:linear-gradient(135deg,#2a2a6a,#c05a8a)"></div><span><i></i>Starblazer</span></div>

<section class="abs perks">
  <div class="perk">
    <svg width="34" height="24" viewBox="0 0 34 24"><rect x="1" y="4" width="20" height="13" fill="#d2171e"/><path d="M21 8h7l4 5v4H21z" fill="#d2171e"/><circle cx="8" cy="19" r="3" fill="#333"/><circle cx="27" cy="19" r="3" fill="#333"/></svg>
    <div><h5>Free Delivery</h5><p>Free delivery and setup on every machine order in our area.</p></div>
  </div>
  <div class="perk">
    <svg width="28" height="28" viewBox="0 0 28 28"><circle cx="14" cy="14" r="12" fill="#7a2a8a"/><path d="M2 14h24M14 2c-6 7-6 17 0 24M14 2c6 7 6 17 0 24" stroke="#fff" stroke-width="1.4" fill="none"/></svg>
    <div><h5>Anytime anywhere</h5><p>Shop online any hour and pick up at our showroom anytime.</p></div>
  </div>
  <div class="perk">
    <svg width="32" height="24" viewBox="0 0 32 24"><rect x="1" y="2" width="30" height="20" rx="3" fill="#444"/><rect x="1" y="7" width="30" height="4" fill="#999"/><rect x="5" y="15" width="9" height="3" fill="#ccc"/></svg>
    <div><h5>Secure Payments</h5><p>Encrypted checkout with financing options for every buyer.</p></div>
  </div>
</section>

<footer class="abs site-footer">
  <div class="newsletter">
    <h6>NEWSLETTER</h6>
    <p>Get new arrivals and showroom events in your inbox.</p>
    <div class="field">Enter your email</div>
    <span class="send">SUBSCRIBE</span>
  </div>
  <div class="col"><h6>CATEGORIES</h6><ul><li>New Pinball</li><li>Used Pinball</li><li>Replacement</li><li>Gadgets</li><li>Accessories</li><li>Games</li></ul></div>
  <div class="col"><h6>INFORMATION</h6><ul><li>About Us</li><li>New Arrivals</li><li>Best Sellers</li><li>Contact Us</li><li>Delivery</li></ul></div>
  <div class="col"><h6>INFORMATION</h6><ul><li>Legal Notice</li><li>Terms and Conditions</li><li>Privacy Policy</li><li>Returns</li><li>Sitemap</li></ul></div>
  <div class="store"><h6>STORE INFORMATION</h6>
    <div class="name">Gadget Arcade</div>
    <ul><li>(602) 555-0187</li><li>hello@gadgetarcade.shop</li></ul>
    <div class="socials"><i></i><i></i><i></i><i></i></div>
  </div>
</footer>

<div class="abs legal"><span></span><span>© 2017 Gadget Arcade. All rights reserved.</span><span>Top</span></div>

</body>
</html>
```